Doors for Chiropractic Office

In my chiropractic office I have 6 treatment rooms and 2 massage rooms. The entire office is going through a remodel. The overall color scheme is very earth tones but in order to add some color, the 6 doors to the treatment rooms will all be a separate color (Red, Blue, Yellow, Green etc)
I need to number each room 1,2,3,4,5,6 and the 2 massage rooms. I had the idea of putting a giant number on each door, so I am looking for some graphic ideas for that project.
The rooms are located with 4 on each side of a long hallway with the 2 massage rooms at the end.
The purpose of numbering each door is to direct the patients where to go.
I have uploaded pictures of the hall way. Pardon the dust since we are under construction but hopefully it gives you an idea of the layout. The door colors will change as stated above.

Requirements
Nice to have
• I would like to see someone come up with a design where each number for the doors are created out of vertebrae's.

```html
<!DOCTYPE html>
<html lang="en">
<head>
<meta charset="utf-8">
<title>Treatment Room Door Graphics</title>
<link rel="stylesheet" href="https://fonts.googleapis.com/css2?family=Roboto+Condensed:wght@700&display=swap">
<style>
  :root {
    --backdrop: #5f5f5f;
    --ink: #ffffff;
    --room-1: #ffcb03;
    --room-2: #f2650a;
    --room-3: #f20303;
    --room-4: #ee2a7d;
    --room-5: #123783;
    --room-6: #05ad9b;
  }
  html, body {
    margin: 0;
    padding: 0;
    width: 1200px;
    height: 1200px;
    overflow: hidden;
    background: var(--backdrop);
  }
  .door-set {
    position: relative;
    width: 1200px;
    height: 1200px;
  }
  .door-panel {
    position: absolute;
    width: 225px;
    height: 501px;
    display: block;
  }
  .door-panel .room-number {
    font-family: "Roboto Condensed", "Arial Narrow", sans-serif;
    font-weight: 700;
    font-size: 540px;
    fill: var(--ink);
  }
  .room-1 { left: 189px; top: 64px; }
  .room-2 { left: 491px; top: 64px; }
  .room-3 { left: 787px; top: 64px; }
  .room-4 { left: 189px; top: 642px; }
  .room-5 { left: 491px; top: 642px; }
  .room-6 { left: 787px; top: 642px; }
</style>
</head>
<body>
<main class="door-set">

  <svg class="door-panel room-1" viewBox="0 0 225 501" aria-label="Room 1 door">
    <rect width="225" height="501" fill="var(--room-1)"/>
    <text class="room-number" x="80" y="501">1</text>
  </svg>

  <svg class="door-panel room-2" viewBox="0 0 225 501" aria-label="Room 2 door">
    <rect width="225" height="501" fill="var(--room-2)"/>
    <text class="room-number" x="36" y="501">2</text>
  </svg>

  <svg class="door-panel room-3" viewBox="0 0 225 501" aria-label="Room 3 door">
    <rect width="225" height="501" fill="var(--room-3)"/>
    <text class="room-number" x="36" y="498">3</text>
  </svg>

  <svg class="door-panel room-4" viewBox="0 0 225 501" aria-label="Room 4 door">
    <rect width="225" height="501" fill="var(--room-4)"/>
    <text class="room-number" x="34" y="498">4</text>
  </svg>

  <svg class="door-panel room-5" viewBox="0 0 225 501" aria-label="Room 5 door">
    <rect width="225" height="501" fill="var(--room-5)"/>
    <text class="room-number" x="67" y="496">5</text>
  </svg>

  <svg class="door-panel room-6" viewBox="0 0 225 501" aria-label="Room 6 door">
    <rect width="225" height="501" fill="var(--room-6)"/>
    <text class="room-number" x="53" y="496">6</text>
  </svg>

</main>
</body>
</html>
```